business card for a massage therapy practice named 'Cedar and Willow Massage Studio'

I really need a trendy, yet easy on the eyes business card to complement my logo. Ideally with some gold or rose gold foil work.

My uploaded file of the logo I have in horizontal but I have a vertical version as well. Another color that is used in the website is a blush pink here and there. I'd like to see some trendy tropical leaves in the design.

```html
<!DOCTYPE html>
<html lang="en">
<head>
<meta charset="UTF-8">
<title>Cedar and Willow Massage Studio – Business Card</title>
<link href="https://fonts.googleapis.com/css2?family=Open+Sans:wght@400;600&display=swap" rel="stylesheet">
<style>
  :root {
    --canvas-bg: #e9e8e6;
    --card-white: #ffffff;
    --card-dark: #4b4b4e;
    --card-dark-top: #3f3f42;
    --teal: #5cc8b0;
    --ink: #2b2b2b;
    --gold: #a8956a;
    --photo-grey: #9c9c9e;
    --photo-skin: #d9b6a3;
  }
  * { box-sizing: border-box; margin: 0; padding: 0; }
  html, body { width: 1200px; height: 782px; overflow: hidden; }
  body {
    background: var(--canvas-bg);
    font-family: "Open Sans", Arial, sans-serif;
    position: relative;
  }
  .card {
    position: absolute;
    top: 241px;
    width: 525px;
    height: 300px;
    overflow: hidden;
    box-shadow: 0 6px 18px rgba(0,0,0,0.18);
  }
  /* Front */
  .card-front { left: 50px; background: var(--card-white); border-bottom: 6px solid var(--gold); }
  .holder-name {
    position: absolute; left: 32px; top: 34px;
    color: var(--teal); font-size: 16px; font-weight: 400; letter-spacing: 0.5px;
    text-transform: uppercase;
  }
  .holder-title {
    position: absolute; left: 32px; top: 56px;
    color: var(--ink); font-size: 13px;
  }
  .studio-mark {
    position: absolute; left: 218px; top: 128px;
    display: flex; align-items: center; gap: 12px;
  }
  .studio-dot { width: 34px; height: 34px; border-radius: 50%; background: var(--gold); flex: none; }
  .studio-name {
    color: var(--ink); font-size: 21px; font-weight: 600; line-height: 1.15;
  }
  .contact {
    position: absolute; left: 32px; top: 200px;
    list-style: none; color: var(--ink); font-size: 14px; line-height: 21px;
  }
  .contact li { display: flex; align-items: center; gap: 6px; }
  .contact svg { width: 12px; height: 12px; fill: var(--teal); flex: none; }
  .address {
    position: absolute; right: 28px; bottom: 18px;
    text-align: right; color: var(--ink); font-size: 15px; line-height: 21px; font-style: normal;
  }
  /* Back */
  .card-back {
    left: 625px;
    background: linear-gradient(180deg, var(--card-dark-top), var(--card-dark));
  }
  .services {
    position: absolute; left: 40px; top: 36px;
    list-style: none; color: #fff; font-size: 11.5px; line-height: 18px;
    text-transform: uppercase; letter-spacing: 0.3px; z-index: 2;
  }
  .services li { display: flex; align-items: center; gap: 8px; }
  .services li::before {
    content: ""; width: 6px; height: 6px; border-radius: 50%; background: var(--teal); flex: none;
  }
  .social { position: absolute; left: 40px; top: 178px; display: flex; gap: 7px; z-index: 2; }
  .social span { width: 18px; height: 18px; border-radius: 50%; background: #fff; display: block; }
  .photo {
    position: absolute; left: 190px; top: 96px; width: 335px; height: 204px;
    background: linear-gradient(135deg, var(--photo-grey) 0%, #b8aaa2 45%, var(--photo-skin) 75%, #8a5a45 100%);
    clip-path: polygon(18% 0, 100% 0, 100% 100%, 0 100%, 0 58%);
  }
</style>
</head>
<body>
  <section class="card card-front" aria-label="Business card front">
    <p class="holder-name">Marisol Vega</p>
    <p class="holder-title">Massage Therapist</p>
    <div class="studio-mark">
      <span class="studio-dot"></span>
      <p class="studio-name">Cedar and Willow<br>Massage Studio</p>
    </div>
    <ul class="contact">
      <li><svg viewBox="0 0 24 24" aria-hidden="true"><path d="M6.6 10.8a15 15 0 0 0 6.6 6.6l2.2-2.2a1 1 0 0 1 1-.25 11.4 11.4 0 0 0 3.6.6 1 1 0 0 1 1 1V20a1 1 0 0 1-1 1A17 17 0 0 1 3 4a1 1 0 0 1 1-1h3.5a1 1 0 0 1 1 1c0 1.25.2 2.45.6 3.6a1 1 0 0 1-.25 1z"/></svg>(555) 014-2387</li>
      <li><svg viewBox="0 0 24 24" aria-hidden="true"><path d="M2 5h20v14H2z M4 7v.5l8 5 8-5V7l-8 5z" fill-rule="evenodd"/></svg>cedarandwillow@mail.com</li>
    </ul>
    <address class="address">2140 Linden Ave. suite 210<br>Riverton, CA 95000</address>
  </section>

  <section class="card card-back" aria-label="Business card back">
    <ul class="services">
      <li>Clinical Bodywork</li>
      <li>Therapeutic Massage</li>
      <li>Integrated Hot Stone Massage</li>
      <li>Lymphatic Drainage Massage</li>
      <li>Riverton Sinus Facial</li>
      <li>Australian Foot Treatment</li>
    </ul>
    <div class="social" aria-label="Social media links">
      <span></span><span></span><span></span><span></span>
    </div>
    <div class="photo" role="img" aria-label="Photo of a therapist's hands massaging a client's neck and shoulders"></div>
  </section>
</body>
</html>
```